Hot Consulting firm collateral upgrade

We need a stationary design for our Oakland based consulting company called Talvora. We provide consulting expertise in KLT compliance for Medical Device, Pharmaceutical, and Biotech companies. We will be using the stationary for all of our marketing collateral. We want the design to convey professionalism and quality. You can find our company color scheme from our website talvora-advisory.com. I have included a copy of our current stationary that needs an upgrade.
Target Market(s)
Medical Device, Pharma, and Biotech companies
Industry/Entity Type
It Company
Look and feel

```html
<!DOCTYPE html>
<html lang="en">
<head>
<meta charset="utf-8">
<title>Talvora Business Card</title>
<link rel="stylesheet" href="https://fonts.googleapis.com/css2?family=Didact+Gothic&family=Montserrat:wght@600&display=swap">
<style>
  :root {
    --brand-blue: #0a4a8a;
    --band-blue: #1558a8;
    --ink-grey: #4a4a4a;
    --text-grey: #5a5a5a;
    --sweep-grey: #555555;
    --card-white: #ffffff;
    --stage: #e4e5e7;
  }
  * { box-sizing: border-box; margin: 0; padding: 0; }
  html, body { width: 1200px; height: 1000px; overflow: hidden; }
  body {
    background: var(--stage);
    font-family: "Didact Gothic", "Century Gothic", sans-serif;
    display: flex;
    flex-direction: column;
    align-items: center;
    justify-content: center;
    gap: 60px;
  }
  .card {
    position: relative;
    width: 630px;
    height: 360px;
    overflow: hidden;
    box-shadow: 0 6px 18px rgba(0,0,0,0.12);
  }

  /* Back side */
  .card-back { background: var(--brand-blue); }
  .back-brand {
    position: absolute;
    left: 50%; top: 50%;
    transform: translate(-50%, -50%);
    color: var(--card-white);
    font-size: 62px;
    letter-spacing: 1px;
    white-space: nowrap;
  }

  /* Front side */
  .card-front { background: var(--card-white); }
  .front-wave { position: absolute; left: 0; bottom: 0; width: 100%; height: 160px; }
  .company-block {
    position: absolute;
    left: 48px; top: 50px;
  }
  .front-brand {
    color: var(--ink-grey);
    font-size: 50px;
    letter-spacing: 1px;
    white-space: nowrap;
  }
  .address {
    margin-top: 14px;
    font-size: 14px;
    line-height: 1.45;
    color: var(--text-grey);
  }
  .contact-block {
    position: absolute;
    left: 350px; top: 148px;
  }
  .person-name {
    font-family: "Montserrat", sans-serif;
    font-weight: 600;
    font-size: 16px;
    letter-spacing: 1px;
    color: var(--brand-blue);
    text-transform: uppercase;
  }
  .person-title {
    font-size: 14px;
    color: var(--text-grey);
    margin-bottom: 10px;
  }
  .contact-list { list-style: none; }
  .contact-item {
    display: flex;
    align-items: center;
    gap: 8px;
    font-size: 14px;
    line-height: 1.55;
    color: var(--text-grey);
    white-space: nowrap;
  }
  .contact-icon { width: 13px; height: 13px; flex: none; }
</style>
</head>
<body>

  <section class="card card-back" aria-label="Business card back">
    <div class="back-brand">Talvora</div>
  </section>

  <section class="card card-front" aria-label="Business card front">
    <svg class="front-wave" viewBox="0 0 630 160" preserveAspectRatio="none" aria-hidden="true">
      <path d="M0 8 C 220 18, 420 128, 630 140 L 630 160 L 0 160 Z" fill="var(--band-blue)"/>
      <path d="M0 13 C 210 26, 390 132, 560 160 L 0 160 Z" fill="var(--card-white)"/>
      <path d="M0 30 C 140 48, 250 110, 320 160 L 0 160 Z" fill="var(--sweep-grey)"/>
    </svg>

    <div class="company-block">
      <div class="front-brand">Talvora</div>
      <p class="address">Bay Area HQ<br>2240 Harborline Street<br>Oakland, CA 94607</p>
    </div>

    <div class="contact-block">
      <p class="person-name">Jordan Ellery</p>
      <p class="person-title">Account Executive</p>
      <ul class="contact-list">
        <li class="contact-item">
          <svg class="contact-icon" viewBox="0 0 13 13" aria-hidden="true">
            <rect width="13" height="13" rx="2" fill="var(--brand-blue)"/>
            <path d="M4 3 L5.5 3 L6 5 L5 5.8 C5.5 7 6 7.5 7.2 8 L8 7 L10 7.5 L10 9 C7 9.5 3.5 6 4 3 Z" fill="#fff"/>
          </svg>
          (510) 555-0142
        </li>
        <li class="contact-item">
          <svg class="contact-icon" viewBox="0 0 13 13" aria-hidden="true">
            <rect width="13" height="13" rx="2" fill="var(--brand-blue)"/>
            <rect x="3" y="4" width="7" height="5" fill="none" stroke="#fff" stroke-width="1"/>
            <path d="M3 4 L6.5 7 L10 4" fill="none" stroke="#fff" stroke-width="1"/>
          </svg>
          info@talvora-advisory.com
        </li>
        <li class="contact-item">
          <svg class="contact-icon" viewBox="0 0 13 13" aria-hidden="true">
            <rect width="13" height="13" rx="2" fill="var(--brand-blue)"/>
            <circle cx="6.5" cy="6.5" r="3.5" fill="none" stroke="#fff" stroke-width="1"/>
            <path d="M3 6.5 H10 M6.5 3 C5 5, 5 8, 6.5 10 M6.5 3 C8 5, 8 8, 6.5 10" fill="none" stroke="#fff" stroke-width="0.8"/>
          </svg>
          www.talvora-advisory.com
        </li>
      </ul>
    </div>
  </section>

</body>
</html>
```